Company or website name
- dalewintham.com
- Links to the website
- Vita Forge
- Describe your company and organization and target audience
- Founded by celebrity personal trainer and media personality Dale Wintham, Vita Forge provides high quality on-site fitness and wellness classes, and personal trainers for businesses and residential gyms throughout New York City. Our target audience are residents of high end buildings in NYC, that expect excellence and luxury
- The design should have the following
- This is a 24"x36" Poster for a complimentary event at a high end building. I would like the poster to look high end, luxury and simple and chique. The words should be clear and easy to read. It would be great to have a final copy that we can send to the printer and one which we can edit for future events Here is the text: The Halcott Spires Gym Complimentary Fitness & Wellness Event Complimentary Yoga, Pilates & Interval Training Bootcamp Classes PLUS: 30 Minute Private Training Sessions *Kids Karate Classes Also Available Saturday May 18th, 25th & June 1st Time: 9:00am - 12:15pm Halcott Spires Gym Schedule: 9:00am - 9:30am Yoga 9:45am - 10:15am Interval Training Bootcamp 11:45am -12:15pm Pilates 9:00am - 12:00pm Private Training Sessions Special Introductory Rate on Future Packages During Promotion www.Vitaforge.tv Info@vitaforge.tv
- Other Facts

```html
<!DOCTYPE html>
<html lang="en">
<head>
<meta charset="utf-8">
<title>Halcott Spires Gym – Complimentary Fitness &amp; Wellness Event</title>
<link rel="stylesheet" href="https://fonts.googleapis.com/css2?family=Oswald:wght@600;700&family=Open+Sans:wght@600;700&display=swap">
<style>
  :root {
    --ink: #050505;
    --white: #ffffff;
    --lime: #e4e000;
    --leaf: #7cb51c;
    --forest: #2f8a16;
    --deep-green: #1c5e12;
    --olive-yellow: #c9c400;
    --circle-top: #b2cc1c;
    --circle-bottom: #3a9418;
    --skin-light: #b07a52;
    --skin-mid: #7a4c32;
    --skin-dark: #2a1a12;
  }
  html, body {
    margin: 0;
    padding: 0;
    overflow: hidden;
    background: var(--ink);
  }
  .poster {
    position: relative;
    width: 800px;
    height: 1200px;
    overflow: hidden;
    background: radial-gradient(ellipse at 55% 45%, #1e1e1e 0%, var(--ink) 70%);
    font-family: "Open Sans", Arial, sans-serif;
    color: var(--white);
  }
  .swooshes, .class-badges {
    position: absolute;
    left: 0;
    top: 0;
  }
  .hero-photo {
    position: absolute;
    left: 140px;
    top: 128px;
  }

  .headline {
    position: absolute;
    top: 28px;
    left: 0;
    width: 800px;
    margin: 0;
    text-align: center;
    font-family: "Oswald", "Arial Narrow", sans-serif;
    font-weight: 700;
    line-height: 1.12;
    letter-spacing: -0.5px;
    text-shadow: 3px 4px 3px rgba(0,0,0,0.75);
  }
  .headline .line-one { display: block; font-size: 44px; padding-left: 8px; }
  .headline .lead-word { font-size: 32px; }
  .headline .line-two { display: block; font-size: 44px; padding-left: 6px; }

  .badge-label {
    font-family: "Oswald", "Arial Narrow", sans-serif;
    font-weight: 700;
    fill: var(--white);
    text-anchor: middle;
  }

  .bonus-count {
    position: absolute;
    left: 24px;
    top: 734px;
    width: 110px;
    text-align: center;
    font-family: "Oswald", "Arial Narrow", sans-serif;
    font-weight: 700;
    line-height: 1;
  }
  .bonus-count .plus { display: block; font-size: 33px; }
  .bonus-count .number { display: block; font-size: 88px; color: var(--olive-yellow); letter-spacing: -4px; margin-top: -4px; line-height: 0.92; }
  .bonus-count .unit { display: block; font-size: 31px; margin-top: 2px; }

  .bonus-offer {
    position: absolute;
    left: 149px;
    top: 744px;
    text-shadow: 1px 2px 3px rgba(0,0,0,0.6);
  }
  .bonus-offer h2 {
    margin: 0;
    font-size: 50px;
    font-weight: 700;
    line-height: 1.1;
    letter-spacing: -0.5px;
  }
  .bonus-offer p {
    margin: 2px 0 0;
    font-size: 23.5px;
    font-weight: 700;
    line-height: 1.38;
  }

  .schedule {
    position: absolute;
    left: 29px;
    top: 1064px;
    width: 560px;
  }
  .schedule h3 {
    margin: 0 0 5px;
    width: 451px;
    font-size: 17px;
    font-weight: 700;
    letter-spacing: 0.5px;
    border-bottom: 2px solid var(--white);
    line-height: 1.1;
  }
  .schedule ul {
    list-style: none;
    margin: 0;
    padding: 0;
    font-size: 13.6px;
    font-weight: 700;
    line-height: 19.5px;
  }
</style>
</head>
<body>
<main class="poster">

  <svg class="swooshes" width="800" height="1200" viewBox="0 0 800 1200" aria-hidden="true">
    <defs>
      <linearGradient id="band-left" x1="0" y1="0" x2="0" y2="1">
        <stop offset="0" stop-color="var(--lime)"/>
        <stop offset="1" stop-color="var(--leaf)"/>
      </linearGradient>
      <linearGradient id="band-right" x1="0" y1="0" x2="0" y2="1">
        <stop offset="0" stop-color="var(--lime)"/>
        <stop offset="0.55" stop-color="var(--leaf)"/>
        <stop offset="1" stop-color="var(--forest)"/>
      </linearGradient>
      <linearGradient id="band-base" x1="0" y1="0" x2="1" y2="0">
        <stop offset="0" stop-color="var(--forest)"/>
        <stop offset="0.6" stop-color="var(--deep-green)"/>
        <stop offset="1" stop-color="#14400d"/>
      </linearGradient>
    </defs>
    <path d="M0 290 C60 140 200 40 380 0 L470 0 C240 80 60 260 0 560 Z" fill="url(#band-left)"/>
    <path d="M0 1000 C220 1100 520 1120 800 1040 L800 1200 L0 1200 Z" fill="url(#band-base)"/>
    <path d="M680 0 L800 0 L800 560 C780 860 560 1100 180 1200 L60 1200 C470 1080 740 820 770 460 C790 240 760 90 680 0 Z" fill="url(#band-right)"/>
  </svg>

  <svg class="hero-photo" width="420" height="910" viewBox="0 0 420 910" role="img" aria-label="Photo of a smiling athlete in black sportswear throwing a punch mid-stride, with faded motion echoes behind her">
    <defs>
      <linearGradient id="athlete-tone" x1="0" y1="0" x2="1" y2="0">
        <stop offset="0" stop-color="var(--skin-dark)" stop-opacity="0.9"/>
        <stop offset="0.3" stop-color="var(--skin-light)" stop-opacity="0.9"/>
        <stop offset="0.55" stop-color="var(--skin-mid)" stop-opacity="0.85"/>
        <stop offset="0.8" stop-color="var(--skin-dark)" stop-opacity="0.7"/>
        <stop offset="1" stop-color="var(--skin-dark)" stop-opacity="0.3"/>
      </linearGradient>
    </defs>
    <rect x="0" y="0" width="420" height="910" rx="60" fill="url(#athlete-tone)"/>
  </svg>

  <h1 class="headline">
    <span class="line-one"><span class="lead-word">The</span> Halcott Spires Gym Complimentary</span>
    <span class="line-two">Fitness &amp; Wellness Event</span>
  </h1>

  <svg class="class-badges" width="800" height="1200" viewBox="0 0 800 1200" aria-label="Complimentary classes">
    <defs>
      <linearGradient id="badge-fill" x1="0" y1="0" x2="0" y2="1">
        <stop offset="0" stop-color="var(--circle-top)"/>
        <stop offset="1" stop-color="var(--circle-bottom)"/>
      </linearGradient>
    </defs>
    <g stroke="var(--white)" stroke-width="5" fill="url(#badge-fill)">
      <circle cx="640" cy="256" r="99"/>
      <circle cx="547" cy="400" r="80"/>
      <circle cx="685" cy="400" r="80"/>
    </g>
    <text class="badge-label" x="640" y="254" font-size="27">Complimentary</text>
    <text class="badge-label" x="640" y="295" font-size="44">Yoga</text>
    <text class="badge-label" x="547" y="369" font-size="21">Interval</text>
    <text class="badge-label" x="547" y="397" font-size="21">Training</text>
    <text class="badge-label" x="547" y="425" font-size="21">Bootcamp</text>
    <text class="badge-label" x="547" y="453" font-size="21">Classes</text>
    <text class="badge-label" x="686" y="414" font-size="38">Pilates</text>
  </svg>

  <div class="bonus-count">
    <span class="plus">PLUS:</span>
    <span class="number">30</span>
    <span class="unit">MINUTE</span>
  </div>

  <section class="bonus-offer">
    <h2>Private Training Sessions</h2>
    <p>Special Introductory Rate on Future Packages<br>During Promotion</p>
  </section>

  <section class="schedule">
    <h3>SCHEDULE</h3>
    <ul>
      <li>Halcott Spires Gym 9:00am - 9:30am | Yoga 9:45am - 10:15am</li>
      <li>Interval Training Bootcamp 11:45am -12:15pm | Pilates 9:00am - 12:00pm</li>
      <li>Kids Karate Classes Also Available</li>
      <li>Saturday May 18th, 25th &amp; June 1st &nbsp;@9:00am - 12:15pm</li>
      <li>www.Vitaforge.tv | Info@vitaforge.tv</li>
    </ul>
  </section>

</main>
</body>
</html>
```